Tellmora Corporate Stationery

Look for design of all new corporate stationery for an existing insurance broking business that is going through a redesign and move from older partners to younger family members. New Logo is attached. Company is Brisbane based.
Colours in the Logo is Hex #43bed8 and website features a lot of hex #17b8d8. Website front page "A plan to protect you" - headline. "Professional and Individual advice to protect your greatest assets" - tagline.

Stationery required: Business Cards, Letter head, Thank-you cards, Birthday cards, Presentation folders, With Compliment slips and a powerpoint template. We also would like to send a card to all customers with the something along of the lines of "something new".

Target Market(s)

Customers of Insurance business looking at superannuation, life and income protection insurance, investment advice and wills

Industry/Entity Type

Insurance Broker

Font styles to use
Other font styles liked:
• same as logo

Requirements
Must have
• The above designs for new stationery for the new business including:
• Business Cards, Letter head, Thank-you cards, Birthday cards, Presentation folders, With Compliment slips and a powerpoint template. We also would like to send a card to all customers with the something along of the lines of "something new".
Nice to have
• It is a new look - long time family business being passed to next generation - big focus on advice for YOU, individual advice etc..

```html
<!DOCTYPE html>
<html lang="en">
<head>
<meta charset="utf-8">
<title>Tellmora Financial Group — Letterhead</title>
<link href="https://fonts.googleapis.com/css2?family=Questrial&display=swap" rel="stylesheet">
<style>
  :root {
    --stage: #c3e9ec;
    --paper: #ffffff;
    --brand-teal: #17b8d8;
    --logo-teal: #43bed8;
    --teal-deep: #2a9fc0;
    --ink-grey: #6d6f73;
    --bar-grey: #8f9094;
    --bar-grey-light: #e6e6e7;
    --rule-grey: #d4d5d7;
    --tagline: #7fd0e2;
  }
  * { box-sizing: border-box; margin: 0; padding: 0; }
  html, body {
    width: 1200px; height: 784px; overflow: hidden;
    background: var(--stage);
    font-family: "Questrial", sans-serif;
  }
  .letterhead {
    position: absolute; left: 338px; top: 22px;
    width: 523px; height: 740px;
    background: var(--paper);
    overflow: hidden;
    box-shadow: 0 6px 18px rgba(40, 110, 120, 0.18);
  }

  /* top edge: grey bar, then teal contact panel */
  .edge-top-grey {
    position: absolute; left: 0; top: 0; width: 196px; height: 8px;
    background: linear-gradient(180deg, var(--bar-grey), var(--bar-grey-light));
  }
  .edge-top-rule {
    position: absolute; left: 0; top: 12px; width: 190px; height: 1px;
    background: var(--rule-grey);
  }
  .contact-panel {
    position: absolute; right: 0; top: 0;
    width: 318px; height: 78px;
    background: linear-gradient(90deg, var(--teal-deep), var(--brand-teal));
    color: #fff;
    padding: 12px 16px 0 92px;
    font-size: 7.5px; line-height: 1.55; letter-spacing: 0.03em;
  }
  .contact-name { font-size: 9.5px; letter-spacing: 0.08em; text-transform: uppercase; margin-bottom: 2px; }
  .contact-line { display: flex; align-items: center; gap: 5px; white-space: nowrap; }
  .contact-line svg { width: 7px; height: 7px; flex: none; }
  .contact-rule {
    position: absolute; right: 0; top: 84px; width: 324px; height: 1px;
    background: var(--rule-grey);
  }

  /* brand name */
  .brand {
    position: absolute; left: 22px; top: 24px;
    display: flex; align-items: center; gap: 10px;
  }
  .brand-dot { width: 26px; height: 26px; border-radius: 50%; background: var(--ink-grey); }
  .brand-name {
    font-size: 24px; color: var(--logo-teal);
    letter-spacing: 0.1em; text-transform: uppercase;
  }

  /* bottom edge: teal bar, then grey bar */
  .edge-bottom-teal {
    position: absolute; left: 0; bottom: 0; width: 318px; height: 7px;
    background: var(--brand-teal);
  }
  .edge-bottom-rule {
    position: absolute; left: 0; bottom: 12px; width: 150px; height: 1px;
    background: var(--rule-grey);
  }
  .edge-bottom-teal-inner {
    position: absolute; left: 150px; bottom: 11px; width: 168px; height: 3px;
    background: var(--brand-teal);
  }
  .edge-bottom-grey {
    position: absolute; right: 0; bottom: 0; width: 186px; height: 18px;
    background: linear-gradient(0deg, var(--bar-grey), var(--bar-grey-light));
  }

  /* tagline running down the right edge */
  .tagline {
    position: absolute; right: 14px; top: 108px;
    height: 600px;
    writing-mode: vertical-rl;
    font-size: 10px; color: var(--tagline);
    letter-spacing: 0.03em; text-transform: uppercase; white-space: nowrap;
  }
</style>
</head>
<body>
  <main class="letterhead">
    <div class="edge-top-grey"></div>
    <div class="edge-top-rule"></div>

    <header class="brand">
      <span class="brand-dot"></span>
      <span class="brand-name">Tellmora</span>
    </header>

    <aside class="contact-panel">
      <div class="contact-name">Tellmora Financial Group</div>
      <div class="contact-line">
        <svg viewBox="0 0 10 10"><path d="M5 0a3.5 3.5 0 0 0-3.5 3.5C1.5 6 5 10 5 10s3.5-4 3.5-6.5A3.5 3.5 0 0 0 5 0zm0 5a1.5 1.5 0 1 1 0-3 1.5 1.5 0 0 1 0 3z" fill="#fff"/></svg>
        Suite 100, 24 Carrow Lane, Brisbane QLD 4000
      </div>
      <div class="contact-line">
        <svg viewBox="0 0 10 10"><path d="M2 0l2 2.5-1 1.2a6 6 0 0 0 3.3 3.3l1.2-1L10 8 8.5 10C4 10 0 6 0 1.5z" fill="#fff"/></svg>
        (07) 3000 0271
      </div>
      <div class="contact-line">
        <svg viewBox="0 0 10 10"><rect x="1" y="3" width="8" height="5" fill="#fff"/><rect x="3" y="1" width="4" height="2" fill="#fff"/></svg>
        (07) 3000 0274
      </div>
      <div class="contact-line">
        <svg viewBox="0 0 10 10"><circle cx="5" cy="5" r="4" fill="none" stroke="#fff"/><path d="M1 5h8M5 1c-2 2.5-2 5.5 0 8M5 1c2 2.5 2 5.5 0 8" fill="none" stroke="#fff" stroke-width="0.8"/></svg>
        www.tellmorafinancial.com.au
      </div>
    </aside>
    <div class="contact-rule"></div>

    <p class="tagline">A plan to protect you &nbsp;-&nbsp; Professional and individual advice to protect your greatest assets</p>

    <div class="edge-bottom-rule"></div>
    <div class="edge-bottom-teal-inner"></div>
    <div class="edge-bottom-teal"></div>
    <div class="edge-bottom-grey"></div>
  </main>
</body>
</html>
```